Landing Page Design for Adult Dating Age Verification (18+)

The objective of this task is to design a visually appealing pre-landing page for the adult dating site "Quillmera (site: https://quillmera.com/)" with an age verification mechanism. The pre-landing page will feature two buttons that redirect visitors to the main offer. The design should also include a footer block that includes links to the terms of use, privacy policy, and contact us pages.

Design Requirements:
Develop an age verification section prominently displayed on the pre-landing page.
Design the section to include two buttons labeled "Yes" and "No" for visitors to confirm their age.
Ensure the section is visually appealing and clearly communicates the purpose of age verification.

Visual Appeal:
Create a visually appealing design that aligns with the branding and theme of the "Quillmera" adult dating site.
Use suitable color schemes, typography, and graphics to enhance the overall visual appeal of the pre-landing page.

Layout and Navigation:
Design an engaging and intuitive layout that encourages visitors to interact with the page and proceed to the main offer.
Ensure clear and visible navigation elements that direct visitors to the main offer or provide additional information.

Responsive Design:
Develop a responsive design that provides a seamless user experience across various devices, including desktop and mobile.
Ensure the design elements and layout adapt well to different screen sizes and resolutions.

File Formats and Assets:
Deliver the final design in PSD, AI, or Sketch format, ensuring that the files are well-organized and layered.
Include any necessary images or assets used in the design, ensuring they are of high quality and optimized for web use.

```html
<!DOCTYPE html>
<html lang="en">
<head>
<meta charset="utf-8">
<title>Quillmera — Age Verification</title>
<link href="https://fonts.googleapis.com/css2?family=Playfair+Display:wght@500;600&family=Roboto:wght@400;500&display=swap" rel="stylesheet">
<style>
  :root {
    --lavender: #d9bde0;
    --footer-bg: #0a0509;
    --white: #ffffff;
    --ink: #141414;
    --modal-bg: rgba(228, 233, 238, 0.86);
    --yes: #09b40c;
    --no: #dc1421;
    --rule: #3a3438;
  }
  * { box-sizing: border-box; margin: 0; padding: 0; }
  html, body { width: 1200px; height: 1191px; overflow: hidden; }
  body { font-family: "Roboto", sans-serif; background: var(--footer-bg); color: var(--white); position: relative; }

  .hero { position: absolute; left: 0; top: 0; width: 1200px; height: 874px; overflow: hidden; }
  .hero-photo {
    position: absolute; inset: 0;
    background:
      radial-gradient(ellipse at 50% 40%, rgba(190,140,120,0.55) 0%, rgba(90,55,45,0.2) 45%, transparent 70%),
      linear-gradient(180deg, #4a3128 0%, #3b2a26 45%, #4b3532 70%, #2b2228 100%);
  }
  .brand { position: absolute; display: flex; align-items: center; gap: 12px; }
  .brand-dot { width: 22px; height: 22px; border-radius: 50%; background: var(--lavender); }
  .brand-name { font-family: "Playfair Display", serif; font-weight: 600; color: var(--white); }
  .hero .brand { left: 111px; top: 44px; }
  .hero .brand-name { font-size: 40px; }

  .age-gate {
    position: absolute; left: 249px; top: 381px; width: 702px; height: 287px;
    background: var(--modal-bg); text-align: center;
  }
  .age-gate h1 {
    font-family: "Playfair Display", serif; font-weight: 500; font-size: 45px;
    color: var(--ink); margin-top: 46px; letter-spacing: -0.3px;
  }
  .age-actions { display: flex; justify-content: center; gap: 9px; margin-top: 24px; }
  .btn {
    width: 129px; height: 55px; border: 0; border-radius: 2px;
    font-family: "Roboto", sans-serif; font-weight: 500; font-size: 26px; color: var(--white);
    display: flex; align-items: center; justify-content: center;
  }
  .btn-yes { background: var(--yes); }
  .btn-no { background: var(--no); }
  .remember { display: flex; justify-content: center; align-items: center; gap: 14px; margin-top: 22px;
    font-weight: 500; font-size: 22px; color: #2a2a2a; }
  .remember-box { width: 19px; height: 19px; border-radius: 4px; background: #2a2a2a; }

  .site-footer { position: absolute; left: 0; top: 874px; width: 1200px; height: 317px; }
  .site-footer .brand { left: 50%; top: 68px; transform: translateX(-50%); }
  .site-footer .brand-name { font-size: 36px; }
  .contact { position: absolute; top: 170px; display: flex; align-items: center; gap: 11px; }
  .contact-icon { width: 38px; height: 38px; border: 1.5px solid var(--lavender); border-radius: 50%;
    display: flex; align-items: center; justify-content: center; }
  .contact-label { font-size: 16px; line-height: 23px; }
  .contact-value { font-size: 16px; font-weight: 500; line-height: 23px; }
  .contact-call { left: 133px; }
  .contact-email { left: 492px; }
  .contact-address { left: 851px; }
  .footer-rule { position: absolute; left: 111px; top: 246px; width: 977px; height: 1px; background: var(--rule); }
  .footer-bottom { position: absolute; left: 111px; top: 268px; width: 977px; display: flex; justify-content: space-between; font-size: 16px; }
  .footer-bottom a { color: var(--white); text-decoration: none; }
  .sep { margin: 0 12px; }
</style>
</head>
<body>
  <section class="hero">
    <div class="hero-photo" role="img" aria-label="Photograph of an embracing couple in a warm loft bedroom"></div>
    <div class="brand"><span class="brand-dot"></span><span class="brand-name">Quillmera</span></div>
    <div class="age-gate">
      <h1>Are You over 18 years of age?</h1>
      <div class="age-actions">
        <a class="btn btn-yes" href="https://quillmera.com/">Yes</a>
        <a class="btn btn-no" href="#">No</a>
      </div>
      <label class="remember"><span class="remember-box"></span>Remember Me</label>
    </div>
  </section>

  <footer class="site-footer">
    <div class="brand"><span class="brand-dot"></span><span class="brand-name">Quillmera</span></div>

    <div class="contact contact-call">
      <span class="contact-icon"><svg width="16" height="16" viewBox="0 0 24 24" fill="none" stroke="#d9bde0" stroke-width="2"><path d="M5 3h4l2 5-2.5 1.5a11 11 0 0 0 6 6L16 13l5 2v4a2 2 0 0 1-2 2A16 16 0 0 1 3 5a2 2 0 0 1 2-2z"/></svg></span>
      <div><div class="contact-label">Call Us</div><div class="contact-value">+1 555 014 2290</div></div>
    </div>
    <div class="contact contact-email">
      <span class="contact-icon"><svg width="16" height="16" viewBox="0 0 24 24" fill="none" stroke="#d9bde0" stroke-width="2"><rect x="3" y="5" width="18" height="14" rx="2"/><path d="M3 7l9 6 9-6"/></svg></span>
      <div><div class="contact-label">Email Us</div><div class="contact-value">info@quillmera.com</div></div>
    </div>
    <div class="contact contact-address">
      <span class="contact-icon"><svg width="16" height="16" viewBox="0 0 24 24" fill="none" stroke="#d9bde0" stroke-width="2"><path d="M12 22s7-7 7-12a7 7 0 0 0-14 0c0 5 7 12 7 12z"/><circle cx="12" cy="10" r="2.5"/></svg></span>
      <div><div class="contact-label">Address</div><div class="contact-value">23,orem ipsum dolor ametd</div></div>
    </div>

    <div class="footer-rule"></div>
    <div class="footer-bottom">
      <div>© 2023 Quillmera<span class="sep">|</span>All Rights Reserved.</div>
      <div><a href="#">Terms of use</a><span class="sep">|</span><a href="#">Privacy policy</a></div>
    </div>
  </footer>
</body>
</html>
```